Business Card for Vorla Parts Wholesale supplier

Hi There! I need a new business card for our company. We are specialized in selling Vorla parts, mostly we sell new LCD screens for Zelnar and Drelks. I would like to see that back in the design.

You can find the colors and logo's on our website: www.hartuvo.nl

Industry/Entity Type

Business

Contact Information for Business Card

My Details:
Tobias Lindqvist

Phone: 0031687203316
E-mail: Tobias@hartuvo.nl

Slogan: "Because Quality Matters"

Font styles to use
Sans Serif

Colors

Designer to choose colors to be used in the design.

Requirements
Must have
• A Black backside with the Hartuvo logo on it. The front side should be clean with only my contact details.
• But I'm also open for something really different or awesome!
Nice to have
• Remember that we are in the parts & repairing industry, So i'll be handing those business cards mainly to repair companies. Maybe you can do something with that thought :)

```html
<!DOCTYPE html>
<html lang="en">
<head>
<meta charset="utf-8">
<title>Hartuvo Business Card</title>
<link href="https://fonts.googleapis.com/css2?family=Rubik:wght@400;500;600;700&display=swap" rel="stylesheet">
<style>
  :root {
    --orange: #f07122;
    --white: #ffffff;
    --ink: #111111;
    --black: #141414;
    --grey: #6b6b6b;
    --backdrop: #c9c9c9;
  }
  * { margin: 0; padding: 0; box-sizing: border-box; }
  html, body { width: 1200px; height: 1000px; overflow: hidden; }
  body {
    background: var(--backdrop);
    display: flex;
    align-items: center;
    justify-content: center;
    gap: 60px;
    font-family: "Rubik", sans-serif;
  }
  .card {
    position: relative;
    width: 520px;
    height: 297px;
    box-shadow: 0 4px 14px rgba(0,0,0,0.25);
    overflow: hidden;
  }
  .brand {
    display: flex;
    align-items: center;
    gap: 10px;
    font-family: "Rubik", sans-serif;
    font-weight: 600;
    letter-spacing: 0.5px;
    line-height: 1;
  }
  .brand-dot { border-radius: 50%; flex: none; }

  /* Front */
  .card-front { background: var(--white); }
  .card-front .brand {
    position: absolute; left: 58px; top: 36px;
    font-size: 40px; color: var(--ink);
  }
  .card-front .brand-dot { width: 32px; height: 32px; background: var(--orange); }
  .holder-name {
    position: absolute; left: 58px; top: 137px;
    font-size: 18px; font-weight: 600; letter-spacing: 0.6px;
    text-transform: uppercase; color: var(--grey);
  }
  .holder-name .surname { color: var(--orange); }
  .contact-band {
    position: absolute; left: 0; right: 0; bottom: 0; height: 122px;
    background: var(--orange); color: var(--white);
  }
  .band-notch {
    position: absolute; left: 54px; top: -1px;
    width: 0; height: 0;
    border-left: 7px solid transparent;
    border-right: 7px solid transparent;
    border-top: 10px solid var(--white);
  }
  .contact-list {
    position: absolute; left: 58px; top: 34px;
    list-style: none; font-size: 13px; line-height: 22px; font-weight: 400;
  }
  .contact-list li { display: flex; align-items: center; gap: 10px; }
  .contact-list svg { width: 11px; height: 11px; fill: var(--white); }
  .web-block {
    position: absolute; right: 56px; top: 34px;
    text-align: center; font-size: 13px; line-height: 22px; font-weight: 400;
  }
  .web-block .web { display: flex; align-items: center; justify-content: center; gap: 8px; }
  .web-block svg { width: 12px; height: 12px; }

  /* Back */
  .card-back {
    background: var(--black);
    display: flex; align-items: center; justify-content: center;
  }
  .card-back .brand { font-size: 52px; color: var(--white); gap: 12px; }
  .card-back .brand-dot { width: 40px; height: 40px; background: var(--orange); }
</style>
</head>
<body>
  <section class="card card-front" aria-label="Front of business card">
    <div class="brand"><span class="brand-dot"></span>hartuvo</div>
    <p class="holder-name">Tobias <span class="surname">Lindqvist</span></p>
    <div class="contact-band">
      <span class="band-notch"></span>
      <ul class="contact-list">
        <li>
          <svg viewBox="0 0 24 24" aria-hidden="true"><path d="M6.6 10.8a15.1 15.1 0 0 0 6.6 6.6l2.2-2.2a1 1 0 0 1 1-.25 11.4 11.4 0 0 0 3.6.57 1 1 0 0 1 1 1V20a1 1 0 0 1-1 1A17 17 0 0 1 3 4a1 1 0 0 1 1-1h3.5a1 1 0 0 1 1 1c0 1.25.2 2.45.57 3.57a1 1 0 0 1-.25 1z"/></svg>
          <span>0031687203316</span>
        </li>
        <li>
          <svg viewBox="0 0 24 24" aria-hidden="true"><path d="M2 5h20v14H2z M2 5l10 8 10-8" fill="none" stroke="#fff" stroke-width="2.4"/></svg>
          <span>Tobias@hartuvo.nl</span>
        </li>
      </ul>
      <div class="web-block">
        <p class="web">
          <svg viewBox="0 0 24 24" aria-hidden="true"><circle cx="14" cy="10" r="6" fill="none" stroke="#fff" stroke-width="2.5"/><path d="M9.5 14.5 3 21" stroke="#fff" stroke-width="3" stroke-linecap="round"/></svg>
          <span>www.hartuvo.nl</span>
        </p>
        <p class="slogan">Because Quality Matters</p>
      </div>
    </div>
  </section>

  <section class="card card-back" aria-label="Back of business card">
    <div class="brand"><span class="brand-dot"></span>hartuvo</div>
  </section>
</body>
</html>
```